Non Profit Company Looking For New Website

The website for Fernvale Quillstone Heritage Society should offer the viewer beautiful photos that inspire condifence and joy and tap into our love of horses.

We would like to see a website that displays trust, quality and confidence. Needs to be responsive and mobile friendly for all browsers and coded for both Android & IOS.

READ ATTACHED WEBSITE TEMPLATE FOR COMPLETE DETAILS ON WHAT WE ARE LOOKING FOR.

Looking for recommmendations if we should use WordPress/WooCommerce for site or Wordpress with Shopify Plug in or just Shopify.

Must be both desktop and mobile friendly with fast page load speed. Need the ability to edit ourselves.

Industry/Entity Type

Non Profit

Coding

Coded - Design and coding required

Number of Pages Required

5+ page

Requirements
Must have
• We would like to see a website that displays trust, quality and confidence. Needs to be responsive and mobile friendly for all browsers and coded for both Android & IOS.

Looking for recommendations if we should use WordPress/WooCommerce for site or Wordpress with Shopify Plug in or just Shopify.

Logo Colour:
Pantone 7621 C

READ TEMPLATE THAT IS ATTACHED
Nice to have
• Like look of this website as a sample:
https://www.quellbrimtorva.com/

Another similar non profit organization
https://pellaworthcindle.com/

```html
<!DOCTYPE html>
<html lang="en">
<head>
<meta charset="utf-8">
<title>Fernvale Quillstone Heritage Society</title>
<link href="https://fonts.googleapis.com/css2?family=Cinzel:wght@700&family=EB+Garamond:wght@400;500&family=Roboto:wght@400;500;700&display=swap" rel="stylesheet">
<style>
:root{
  --green:#0c7a23;
  --red:#c8202f;
  --ink:#1b1b1b;
  --body:#3a3a3a;
  --light:#f6f6f6;
  --line:#d9d9d9;
  --footer:#111111;
}
*{box-sizing:border-box;margin:0;padding:0}
html,body{width:1200px;height:3521px;overflow:hidden}
body{position:relative;font-family:'Roboto',sans-serif;color:var(--body);background:#fff}
.abs{position:absolute}
.display{font-family:'Cinzel',serif;font-weight:700;color:var(--ink);text-transform:uppercase;letter-spacing:0;white-space:nowrap}

.topbar{left:0;top:0;width:1200px;height:38px;background:var(--green);color:#fff;font-size:16px}
.topbar .item{top:9px;display:flex;align-items:center;gap:8px}
.social{right:100px;top:12px;display:flex;gap:14px}
.social span{width:13px;height:13px;border-radius:50%;background:#fff;opacity:.9}

.header{left:0;top:38px;width:1200px;height:137px;background:#fff}
.brand{left:100px;top:20px;width:122px;text-align:center;font-family:'EB Garamond',serif;font-weight:500;color:var(--red);font-size:15px;line-height:17px;text-transform:uppercase}
.nav{left:282px;top:66px;display:flex;gap:40px;font-family:'EB Garamond',serif;font-size:16px;letter-spacing:.4px;text-transform:uppercase;color:#333}
.nav .active{color:var(--red);font-weight:500}
.search{left:1070px;top:72px}

.hero{left:0;top:175px;width:1200px;height:660px}
.hero-photo{left:0;top:0;width:1200px;height:660px}
.hero-text{left:0;top:200px;width:1200px;text-align:center;color:#fff}
.hero-text h1{font-family:'EB Garamond',serif;font-weight:500;font-size:44px;line-height:50px;letter-spacing:1px;text-transform:uppercase}
.hero-text .tag{font-family:'EB Garamond',serif;font-size:27px;color:var(--red);margin-top:24px;text-transform:uppercase}
.hero-text .sub{font-family:'EB Garamond',serif;font-size:20px;margin-top:22px}
.arrow{top:284px;width:38px;height:38px;border-radius:50%;background:var(--green);display:flex;align-items:center;justify-content:center}

.about{left:0;top:834px;width:1200px;height:508px;background:var(--light)}
.about-art{left:109px;top:72px;width:404px;height:346px;border-radius:4px;background:linear-gradient(160deg,#b9a48c 0%,#c5c9a8 55%,#dcdcc8 100%)}
.about-copy{left:581px;top:88px;width:520px}
.about-copy h2{font-size:33px;line-height:41px}
.about-copy p{font-size:15.5px;line-height:27.5px;margin-top:22px;color:#333;width:510px}
.btn{display:inline-flex;align-items:center;justify-content:center;gap:12px;background:var(--red);color:#fff;font-weight:700;font-size:15px;text-transform:uppercase;border-radius:2px;box-shadow:0 3px 6px rgba(0,0,0,.18)}
.about-copy .btn{margin-top:26px;width:157px;height:41px}

.adopt{left:0;top:1342px;width:1200px;height:886px;background:#fff;text-align:center}
.adopt h2{position:absolute;left:0;top:104px;width:1200px;font-size:35px}
.adopt .lead{position:absolute;left:0;top:176px;width:1200px;font-size:15.5px;color:#333}
.tile{width:286px;height:237px;padding:5px;background:#fff;box-shadow:0 0 5px rgba(0,0,0,.18)}
.tile div{width:100%;height:100%}
.adopt .btn{position:absolute;left:521px;top:763px;width:157px;height:41px}

.give{left:0;top:2228px;width:1200px;height:349px;background:linear-gradient(180deg,#93a7b9 0%,#c9cfa9 40%,#8e9a48 70%,#5f7027 100%)}
.give-tint{left:0;top:0;width:520px;height:349px;background:linear-gradient(90deg,rgba(140,70,30,.45),rgba(140,70,30,0))}
.give-copy{left:692px;top:66px;width:430px;color:#fff}
.give-copy h2{color:#fff;font-size:34px}
.give-copy p{font-size:15.5px;line-height:27.5px;margin-top:18px}
.outline-btn{margin-top:26px;width:202px;height:43px;border:1.5px solid #fff;display:flex;align-items:center;justify-content:center;font-weight:700;font-size:15px;text-transform:uppercase}

.contact{left:0;top:2577px;width:1200px;height:620px;background:#fff}
.contact h2{font-size:36px}
.form-col{left:127px;top:80px;width:490px}
.form-col .intro{font-size:15.5px;line-height:26px;margin-top:8px;color:#333}
.field{border:1.5px solid var(--line);font-size:14px;color:#444;padding:14px 11px;background:#fff}
.captcha{left:127px;top:410px;width:205px;height:48px;background:#f9f9f9;border:1px solid #ddd;display:flex;align-items:center;gap:9px;padding-left:8px;font-size:10px;color:#333}
.captcha .box{width:18px;height:18px;border:1.5px solid #aaa;background:#fff}
.captcha .mark{margin-left:auto;margin-right:10px;width:20px;height:20px;background:#d7dde6}
.submit{left:127px;top:474px;width:152px;height:46px}
.info-col{left:772px;top:80px;width:360px}
.info{display:flex;gap:15px}
.info .icon{width:42px;height:42px;border-radius:50%;background:var(--green);display:flex;align-items:center;justify-content:center;flex:none}
.info h4{font-size:15px;font-weight:700;color:var(--ink);text-transform:uppercase;margin-top:2px}
.info p{font-size:15.5px;line-height:31px;color:#333}

.footer{left:0;top:3170px;width:1200px;height:351px}
.footer-brand{left:540px;top:99px;width:120px;text-align:center;font-family:'EB Garamond',serif;font-weight:500;color:var(--red);font-size:15px;line-height:17px;text-transform:uppercase}
.footer-nav{left:0;top:219px;width:1200px;display:flex;justify-content:center;gap:50px;color:#fff;font-size:15.5px}
.footer-rule{left:112px;top:275px;width:976px;height:1px;background:#3a3a3a}
.copyright{left:0;top:300px;width:1200px;text-align:center;color:#fff;font-size:15.5px}
</style>
</head>
<body>

<div class="abs topbar">
  <div class="abs item" style="left:114px">
    <svg width="14" height="14" viewBox="0 0 24 24" fill="#fff"><path d="M6.6 10.8a15 15 0 0 0 6.6 6.6l2.2-2.2c.3-.3.7-.4 1-.2 1.1.4 2.3.6 3.6.6.6 0 1 .4 1 1V20c0 .6-.4 1-1 1A17 17 0 0 1 3 4c0-.6.4-1 1-1h3.5c.6 0 1 .4 1 1 0 1.3.2 2.5.6 3.6.1.3 0 .7-.2 1z"/></svg>
    555-210-4382
  </div>
  <div class="abs item" style="left:284px">
    <svg width="16" height="13" viewBox="0 0 24 18" fill="none" stroke="#fff" stroke-width="2"><rect x="1" y="1" width="22" height="16" rx="2"/><path d="M1 2l11 8 11-8"/></svg>
    hello@fernvalequill.org
  </div>
  <div class="abs social" aria-label="Social links"><span></span><span></span><span></span><span></span></div>
</div>

<header class="abs header">
  <div class="abs brand">Fernvale Quillstone Heritage Society</div>
  <nav class="abs nav">
    <span class="active">Home</span>
    <span>Thoroughbred Aftercare</span>
    <span>Adopt a Horse</span>
    <span>Donate</span>
    <span>Contact Us</span>
  </nav>
  <svg class="abs search" width="16" height="16" viewBox="0 0 24 24" fill="none" stroke="#111" stroke-width="3"><circle cx="10" cy="10" r="7"/><path d="M15 15l7 7"/></svg>
</header>

<section class="abs hero">
  <svg class="abs hero-photo" viewBox="0 0 1200 660" role="img" aria-label="Woman gently touching a dark horse in a sunlit golden meadow">
    <defs>
      <linearGradient id="meadow" x1="0" y1="0" x2="0" y2="1">
        <stop offset="0" stop-color="#7c6a24"/>
        <stop offset=".45" stop-color="#b88a2c"/>
        <stop offset="1" stop-color="#a07a22"/>
      </linearGradient>
    </defs>
    <polygon points="0,0 1200,0 1200,530 597,632 0,530" fill="url(#meadow)"/>
    <polygon points="0,530 597,632 1200,530 1200,545 597,660 0,545" fill="#f6f6f6"/>
    <polygon points="0,530 597,632 1200,530 1145,548 597,660 55,548" fill="var(--green)"/>
  </svg>
  <div class="abs hero-text">
    <h1>Fernvale Quillstone<br>Heritage Society</h1>
    <div class="tag">Retire. Retrain. Rehome.</div>
    <div class="sub">We support and develop retired thoroughbred racehorses for their next chapter in life</div>
  </div>
  <div class="abs arrow" style="left:33px"><svg width="12" height="12" viewBox="0 0 12 12"><path d="M8 1L3 6l5 5" stroke="#fff" stroke-width="2.4" fill="none"/></svg></div>
  <div class="abs arrow" style="left:1130px"><svg width="12" height="12" viewBox="0 0 12 12"><path d="M4 1l5 5-5 5" stroke="#fff" stroke-width="2.4" fill="none"/></svg></div>
</section>

<section class="abs about">
  <div class="abs about-art" role="img" aria-label="Decorative illustration with horse and meadow imagery"></div>
  <div class="abs about-copy">
    <h2 class="display">What is Thoroughbred<br>Aftercare?</h2>
    <p>The health, safety and welfare of our equine athletes does not end at the finish line, and retirement and aftercare are critical to the success of the racing industry. Aftercare is the safe placement of racehorses after their careers as racehorse are completed. Some horses might retire to the breeding shed or broodmare bands, while others are retrained for second careers.</p>
    <div class="btn">Learn More</div>
  </div>
</section>

<section class="abs adopt">
  <h2 class="display">Adopt a Horse</h2>
  <p class="lead">Fernvale Quillstone Heritage Society is committed to helping match you with the perfect horse.</p>
  <div class="abs tile" style="left:150px;top:230px"><div role="img" aria-label="Person stroking a dark horse at a stable door" style="background:linear-gradient(135deg,#3a2a22,#6b4a3a 60%,#8fa4c0)"></div></div>
  <div class="abs tile" style="left:457px;top:230px"><div role="img" aria-label="Man in plaid shirt with a bay horse in a barn" style="background:linear-gradient(135deg,#c9a070,#6c82a8 45%,#6a3a20)"></div></div>
  <div class="abs tile" style="left:763px;top:230px"><div role="img" aria-label="Rider in helmet with a chestnut horse" style="background:linear-gradient(135deg,#8a4a28,#c9c9c9 65%,#f0f0f0)"></div></div>
  <div class="abs tile" style="left:150px;top:488px"><div role="img" aria-label="Horse being washed with a water hose" style="background:linear-gradient(135deg,#5a3e2c,#2c2a28 50%,#8b8f94)"></div></div>
  <div class="abs tile" style="left:457px;top:488px"><div role="img" aria-label="Woman in cowboy hat feeding a white horse" style="background:linear-gradient(135deg,#6a2e22,#d8ccb6 55%,#4a6fa0)"></div></div>
  <div class="abs tile" style="left:763px;top:488px"><div role="img" aria-label="Young rider beside a white horse under blue sky" style="background:linear-gradient(135deg,#eaeaea,#bfc8cf 45%,#3aa0dc)"></div></div>
  <div class="btn">Adopt Now</div>
</section>

<section class="abs give" role="img" aria-label="Chestnut horse with flowing mane standing in a green meadow">
  <div class="abs give-tint"></div>
  <div class="abs give-copy">
    <h2 class="display">Make a Difference</h2>
    <p>Lorem ipsum dolor sit amet, consectetur adipiscing elit, sed do eiusmod tempor incididunt ut labore et dolore magna aliqua. Ut enim ad minim veniam, quis nostrud exercitation ullamco laboris aliquip commod consequat.</p>
    <div class="outline-btn">More Ways to Give</div>
  </div>
</section>

<section class="abs contact">
  <div class="abs form-col">
    <h2 class="display">Contact Us</h2>
    <p class="intro">Have a question orneed more information?<br>Give us a call or use the Below</p>
  </div>
  <div class="abs field" style="left:127px;top:194px;width:235px;height:42px">First Name:</div>
  <div class="abs field" style="left:379px;top:194px;width:236px;height:42px">Last Name:</div>
  <div class="abs field" style="left:127px;top:251px;width:235px;height:42px">Phone Number:</div>
  <div class="abs field" style="left:379px;top:251px;width:236px;height:42px">Email:</div>
  <div class="abs field" style="left:127px;top:309px;width:488px;height:85px">Message:</div>
  <div class="abs captcha"><span class="box"></span>I'm not a robot<span class="mark"></span></div>
  <div class="abs btn submit">Submit
    <svg width="16" height="16" viewBox="0 0 16 16"><circle cx="8" cy="8" r="8" fill="#fff"/><path d="M5 8h6M8 5l3 3-3 3" stroke="#c8202f" stroke-width="2" fill="none"/></svg>
  </div>

  <div class="abs info-col">
    <h2 class="display">Contact Info</h2>
    <div class="info" style="margin-top:40px">
      <div class="icon"><svg width="18" height="18" viewBox="0 0 24 24" fill="#fff"><path d="M6.6 10.8a15 15 0 0 0 6.6 6.6l2.2-2.2c.3-.3.7-.4 1-.2 1.1.4 2.3.6 3.6.6.6 0 1 .4 1 1V20c0 .6-.4 1-1 1A17 17 0 0 1 3 4c0-.6.4-1 1-1h3.5c.6 0 1 .4 1 1 0 1.3.2 2.5.6 3.6.1.3 0 .7-.2 1z"/></svg></div>
      <div><h4>Phone</h4><p>555-210-4382</p></div>
    </div>
    <div class="info" style="margin-top:20px">
      <div class="icon"><svg width="18" height="14" viewBox="0 0 24 18" fill="none" stroke="#fff" stroke-width="2.4"><rect x="1" y="1" width="22" height="16" rx="2"/><path d="M1 2l11 8 11-8"/></svg></div>
      <div><h4>Email</h4><p>hello@fernvalequill.org</p></div>
    </div>
    <div class="info" style="margin-top:20px">
      <div class="icon"><svg width="16" height="20" viewBox="0 0 16 22" fill="#fff"><path d="M8 0a8 8 0 0 0-8 8c0 6 8 14 8 14s8-8 8-14a8 8 0 0 0-8-8zm0 11a3 3 0 1 1 0-6 3 3 0 0 1 0 6z"/></svg></div>
      <div><h4>Address</h4><p>Brightmoor Studio<br>#14, 88 Larchmere Lane<br>Oakridge Falls, AB T0X 1Y2</p></div>
    </div>
  </div>
</section>

<footer class="abs footer">
  <svg class="abs" style="left:0;top:0" width="1200" height="351" viewBox="0 0 1200 351" role="img" aria-label="Silhouettes of running horses on a dark background">
    <polygon points="0,152 597,8 1200,152 1200,351 0,351" fill="#111111"/>
    <polygon points="350,74 597,8 845,74 820,74 597,20 375,74" fill="#0c7a23"/>
  </svg>
  <div class="abs footer-brand">Fernvale Quillstone Heritage Society</div>
  <nav class="abs footer-nav"><span>Home</span><span>Thoroughbred Aftercare</span><span>Adopt a Horse</span><span>Donate</span><span>Contact Us</span></nav>
  <div class="abs footer-rule"></div>
  <div class="abs copyright">©Copyrights 2021 Fernvale Quillstone Heritage Society &nbsp;| &nbsp; All Rights Reserved &nbsp;|</div>
</footer>

</body>
</html>
```